Vale Linebacker Needs a new website!

We need a four page website for a new company based in San Francisco. We help companies connect better with their clients, employees, and vendors by implementing collaborative technology.
Similar Websites
Mist Rangers - http://www.mistrangers.example/
Skyforthing - http://www.skyforthing.example/ - I don't like the the rotating window or the pictures of people. I like the icons used to go to the next pages.
Color Combos
Blues and Yellows - http://www.huepairings.example/palette-sets/96/HuePairing96.html
We prefer graphics over the actual pictures of people in the header. Pictures of people working together in the text is fine.
Web Page Layout
Index
Cloud Advisory Services
Email Everywhere
CRM Implementation
For detailed copy please see this link https://files.paperhold.example/a/widgetladyla.example/document/d/7KtmPzWqAeRbYcNvHsJgLdFxTuQoIeMnBvCxZaSdFgHj/edit
Industry/Entity Type
It Company

```html
<!DOCTYPE html>
<html lang="en">
<head>
<meta charset="utf-8">
<title>Vale Linebacker</title>
<link rel="stylesheet" href="https://fonts.googleapis.com/css2?family=Open+Sans:wght@400;600;700&family=Lato:wght@400;700&display=swap">
<style>
  :root{
    --brand:#2365b5;
    --nav-top:#5b9ae0;
    --nav-bottom:#2d6cbd;
    --ink:#1a1a1a;
    --muted:#555b63;
    --white:#ffffff;
    --footer-top:#4b4b4b;
    --footer-bottom:#151515;
    --btn:#3d3d3d;
  }
  html,body{margin:0;padding:0;overflow:hidden;background:var(--white);}
  .page{position:relative;width:1200px;height:2542px;overflow:hidden;background:var(--white);font-family:"Lato",Arial,sans-serif;color:var(--ink);}
  .abs{position:absolute;}

  .site-header{left:0;top:0;width:1200px;height:132px;}
  .brand{left:139px;top:50px;display:flex;align-items:center;gap:12px;}
  .brand-dot{width:40px;height:40px;border-radius:50%;background:var(--brand);}
  .brand-name{font-family:"Open Sans",sans-serif;font-weight:700;font-size:30px;color:var(--brand);letter-spacing:-.3px;}
  .call{left:720px;top:64px;font-family:"Open Sans",sans-serif;font-size:18px;color:var(--brand);}
  .call b{font-weight:400;color:#333;}
  .login{left:913px;top:56px;width:150px;height:41px;background:var(--btn);color:var(--white);font-family:"Open Sans",sans-serif;font-size:18px;display:flex;align-items:center;box-shadow:0 1px 2px rgba(0,0,0,.4);}
  .login-icon{width:34px;height:41px;display:flex;align-items:center;justify-content:center;border-right:1px solid #555;}
  .login span{margin-left:26px;}

  .main-nav{left:0;top:132px;width:1200px;height:60px;background:linear-gradient(var(--nav-top),var(--nav-bottom));}
  .main-nav a{position:absolute;top:17px;color:var(--white);text-decoration:none;font-family:"Open Sans",sans-serif;font-size:18px;}

  .hero{left:0;top:192px;width:1200px;height:569px;background:radial-gradient(ellipse at 70% 40%,#c9d9e6 0%,#8aa6bd 40%,#2d3e52 80%,#1a2433 100%);}
  .slider{left:542px;top:693px;width:166px;height:26px;background:#e6e8ea;border-radius:3px;display:flex;align-items:center;box-shadow:0 1px 3px rgba(0,0,0,.4);}
  .slider-arrows{width:48px;display:flex;justify-content:center;gap:8px;border-right:1px solid #bbb;font-size:14px;color:#333;}
  .slider-dots{display:flex;gap:8px;margin-left:12px;}
  .slider-dots i{width:8px;height:8px;border-radius:50%;background:#9a9a9a;display:block;}
  .slider-dots i.on{background:#333;}

  .section-title{left:0;width:1200px;text-align:center;font-family:"Open Sans",sans-serif;font-weight:400;font-size:34px;color:var(--brand);margin:0;}
  .section-lead{left:0;width:1200px;text-align:center;font-size:17px;color:var(--ink);margin:0;}

  .feature{width:240px;text-align:center;}
  .feature.wide{width:280px;}
  .feature-icon{width:115px;height:115px;border-radius:50%;background:var(--brand);margin:0 auto;display:flex;align-items:center;justify-content:center;}
  .feature-label{font-family:"Open Sans",sans-serif;font-size:18px;color:var(--brand);margin:48px 0 10px;text-transform:uppercase;}
  .feature-text{font-size:14px;line-height:23px;color:#333;margin:0;}

  .stories{left:0;top:1210px;width:1200px;height:336px;background:var(--brand);}
  .stories-photo{left:149px;top:1261px;width:366px;height:226px;background:linear-gradient(#eef4fa 0%,#8ea9c6 45%,#2f4560 100%);}
  .stories-title{left:534px;top:1254px;font-family:"Open Sans",sans-serif;font-weight:600;font-size:34px;color:var(--white);margin:0;}
  .stories-text{left:534px;top:1313px;width:497px;font-size:14px;line-height:27.6px;color:var(--white);text-align:justify;margin:0;}

  .card{width:280px;}
  .card-photo{width:276px;height:141px;}
  .card-title{font-family:"Open Sans",sans-serif;font-weight:400;font-size:16px;line-height:22px;color:var(--brand);margin:18px 0 16px;}
  .card-text{font-size:13px;line-height:22px;color:var(--muted);margin:0;}

  .site-footer{left:0;top:2351px;width:1200px;height:191px;background:linear-gradient(var(--footer-top),var(--footer-bottom) 60%);}
  .footer-links{left:0;top:2384px;width:1200px;text-align:center;font-family:Arial,sans-serif;font-size:12px;color:var(--white);}
  .copyright{left:166px;top:2454px;font-family:Arial,sans-serif;font-size:11.5px;color:var(--white);}
  .social{left:443px;top:2438px;display:flex;gap:7px;}
  .social i{display:block;width:37px;height:37px;border-radius:50%;background:#f0f0f0;}
  .newsletter{left:809px;top:2446px;width:222px;height:24px;background:var(--white);display:flex;align-items:center;justify-content:space-between;box-sizing:border-box;padding:0 6px 0 8px;}
  .newsletter span{font-family:Arial,sans-serif;font-size:11px;color:#666;}
</style>
</head>
<body>
<div class="page">

  <header class="site-header abs">
    <div class="brand abs"><div class="brand-dot"></div><div class="brand-name">Vale Linebacker</div></div>
    <div class="call abs">CALL : <b>415-555-0186</b></div>
    <a class="login abs">
      <div class="login-icon">
        <svg width="16" height="18" viewBox="0 0 16 18"><circle cx="8" cy="5" r="4" fill="#fff"/><path d="M0 18c0-5 3.5-7 8-7s8 2 8 7z" fill="#fff"/></svg>
      </div>
      <span>LOG IN</span>
    </a>
  </header>

  <nav class="main-nav abs">
    <a style="left:164px">Home</a>
    <a style="left:260px">Cloud Advisory Services</a>
    <a style="left:488px">Email Everywhere</a>
    <a style="left:673px">CRM Implementation</a>
    <a style="left:880px">Why Vale Linebacker</a>
  </nav>

  <div class="hero abs" role="img" aria-label="Business person touching a glowing cloud icon connected to network nodes"></div>
  <div class="slider abs">
    <div class="slider-arrows"><span>&#8249;</span><span>&#8250;</span></div>
    <div class="slider-dots"><i></i><i></i><i class="on"></i><i></i><i></i><i></i></div>
  </div>

  <h2 class="section-title abs" style="top:798px">Our Cloud Services</h2>
  <p class="section-lead abs" style="top:857px">Vale Linebacker provides unrivaled cloud advisory and technology services for the world's leading brands.</p>

  <div class="feature abs" style="left:139px;top:918px">
    <div class="feature-icon"><svg width="52" height="52" viewBox="0 0 52 52"><path d="M26 6l14 16H31v16H21V22h-9z" fill="#fff"/><rect x="10" y="42" width="32" height="5" fill="#fff"/></svg></div>
    <div class="feature-label">Deployment</div>
    <p class="feature-text">Put your cloud program on the<br>path to success with Cloud</p>
  </div>
  <div class="feature abs" style="left:366px;top:918px">
    <div class="feature-icon"><svg width="56" height="48" viewBox="0 0 56 48"><path d="M4 14h36V6l12 12-12 12v-8H4z" fill="#fff"/><path d="M52 34H16v-8L4 38l12 12v-8h36z" fill="#fff" transform="translate(0,-4)"/></svg></div>
    <div class="feature-label">Migration</div>
    <p class="feature-text">Rely on our advisory,<br>implementation and change</p>
  </div>
  <div class="feature abs" style="left:580px;top:918px">
    <div class="feature-icon"><svg width="46" height="46" viewBox="0 0 46 46"><path d="M14 10a17 17 0 1 0 18 0" fill="none" stroke="#fff" stroke-width="5" stroke-linecap="round"/><line x1="23" y1="4" x2="23" y2="22" stroke="#fff" stroke-width="5" stroke-linecap="round"/></svg></div>
    <div class="feature-label">Project Management</div>
    <p class="feature-text">Drive your business forward with<br>innovative, leading-edge</p>
  </div>
  <div class="feature abs" style="left:802px;top:918px">
    <div class="feature-icon"><svg width="72" height="46" viewBox="0 0 72 46"><path d="M16 44a14 14 0 0 1-1-28 18 18 0 0 1 34-6 14 14 0 0 1 13 12 11 11 0 0 1-2 22z" fill="#fff"/><path d="M12 44a10 10 0 0 1 0-20" fill="none" stroke="var(--brand)" stroke-width="3"/></svg></div>
    <div class="feature-label">Training</div>
    <p class="feature-text">Drive your business forward with<br>innovative, leading-edge</p>
  </div>

  <section class="stories abs"></section>
  <div class="stories-photo abs" role="img" aria-label="Silhouettes of business people walking through a bright glass office"></div>
  <h2 class="stories-title abs">Our Success Stories</h2>
  <p class="stories-text abs">Lorem Ipsum is simply dummy text of the printing and typesetting industry. Lorem Ipsum has been the industry's standard dummy text ever since the 1500s, when an unknown printer took a galley of type and scrambled it to make a type specimen book. It has survived not only five centuries, but also the leap into electronic typesetting, remaining essentially unchanged. It was popularised in the 1960s with the release of Letraset sheets</p>

  <h2 class="section-title abs" style="top:1598px">Who We Are</h2>

  <div class="feature abs" style="left:160px;top:1680px">
    <div class="feature-icon"><svg width="54" height="54" viewBox="0 0 54 54"><rect x="6" y="14" width="18" height="18" fill="#fff"/><rect x="26" y="6" width="14" height="14" fill="#fff"/><rect x="38" y="18" width="10" height="10" fill="#fff"/><rect x="18" y="28" width="20" height="20" fill="#fff"/></svg></div>
    <div class="feature-label">Why Us</div>
    <p class="feature-text">We deliver unmatched value to our<br>customers because we take the time to</p>
  </div>
  <div class="feature abs" style="left:473px;top:1680px">
    <div class="feature-icon"><svg width="60" height="48" viewBox="0 0 60 48"><circle cx="30" cy="12" r="8" fill="#fff"/><circle cx="13" cy="17" r="6" fill="#fff"/><circle cx="47" cy="17" r="6" fill="#fff"/><path d="M16 46c0-12 6-18 14-18s14 6 14 18z" fill="#fff"/><path d="M2 40c0-9 5-14 11-14 3 0 5 1 6 2-3 3-4 7-5 12z" fill="#fff"/><path d="M58 40c0-9-5-14-11-14-3 0-5 1-6 2 3 3 4 7 5 12z" fill="#fff"/></svg></div>
    <div class="feature-label">Our Partners</div>
    <p class="feature-text">We deliver unmatched value to our<br>customers because we take the time to</p>
  </div>
  <div class="feature wide abs" style="left:770px;top:1680px">
    <div class="feature-icon"><svg width="60" height="48" viewBox="0 0 60 48"><rect x="4" y="20" width="42" height="22" rx="3" fill="#fff"/><rect x="10" y="34" width="20" height="3" fill="var(--brand)"/><path d="M34 24a8 8 0 0 1 1-16 11 11 0 0 1 20 2 7 7 0 0 1 0 14z" fill="#fff" stroke="var(--brand)" stroke-width="2.5"/></svg></div>
    <div class="feature-label">In The News</div>
    <p class="feature-text">We deliver unmatched value to our<br>customers because we take the time to truly</p>
  </div>

  <article class="card abs" style="left:166px;top:1990px">
    <div class="card-photo" role="img" aria-label="Illustration of a person seated on a cloud among floating devices" style="background:linear-gradient(#cfe6f7,#f4f9fd)"></div>
    <h3 class="card-title">Delivering Efficient and Personal<br>Service With CTI</h3>
    <p class="card-text">By providing agents with critical caller<br>information from the start, Computer Telephony<br>Integration improves efficiency and the overall</p>
  </article>
  <article class="card abs" style="left:461px;top:1990px">
    <div class="card-photo" role="img" aria-label="Businessman touching a digital cloud surrounded by floating tablets" style="background:linear-gradient(135deg,#0b2a4d,#1f5a95 55%,#0d2340)"></div>
    <h3 class="card-title">Delivering Efficient and Personal<br>Service With CTI</h3>
    <p class="card-text">By providing agents with critical caller<br>information from the start, Computer Telephony<br>Integration improves efficiency and the overall</p>
  </article>
  <article class="card abs" style="left:756px;top:1990px">
    <div class="card-photo" role="img" aria-label="Open hand holding a glowing network of connected icons" style="background:linear-gradient(135deg,#1d3d63,#3f7bb3 50%,#10243d)"></div>
    <h3 class="card-title">Delivering Efficient and Personal<br>Service With CTI</h3>
    <p class="card-text">By providing agents with critical caller<br>information from the start, Computer Telephony<br>Integration improves efficiency and the overall</p>
  </article>

  <footer class="site-footer abs"></footer>
  <div class="footer-links abs">Terms of Service | Returns | Policy Privacy | Event | Contact | Blog | Sitemap</div>
  <div class="copyright abs">Copy Right © 2014. All rights reserved.</div>
  <div class="social abs"><i></i><i></i><i></i><i></i><i></i><i></i></div>
  <div class="newsletter abs">
    <span>News Letter</span>
    <svg width="26" height="18" viewBox="0 0 26 18"><rect x="1.5" y="1.5" width="23" height="15" fill="none" stroke="#333" stroke-width="2.5"/><path d="M1.5 1.5l11.5 9 11.5-9" fill="none" stroke="#333" stroke-width="2.5"/></svg>
  </div>

</div>
</body>
</html>
```